Need help in designing new business card utilizing our new logo.

BuildMark Solutions works with Construction Business Owners, Managers & IT Professionals to strengthen software usage and increase user productivity.

Our Construction Accounting and Mobile Field Management Software Clients engage with us in the following areas:

New Software Implementations
Software Re-Implementations
Redesigning Software Usage at the User Level
Project Coordination & Management
Continued Software Support

Old tag line:
Weighing Options - Implementing Solutions

www.buildmark-solutions.example

Ridge 4 is a product, but not needed for a new business card.

```html
<!DOCTYPE html>
<html lang="en">
<head>
<meta charset="utf-8">
<title>BuildMark Solutions – Business Card</title>
<link rel="stylesheet" href="https://fonts.googleapis.com/css2?family=Arimo:wght@400;700&display=swap">
<style>
  :root {
    --stage: #2a2a2c;
    --brand-blue: #2c3494;
    --paper: #ffffff;
    --arc-grey: #c4c4c6;
    --ink-light: #ffffff;
  }
  * { box-sizing: border-box; margin: 0; padding: 0; }
  html, body { width: 1200px; height: 880px; overflow: hidden; }
  body {
    background: var(--stage);
    font-family: "Arimo", Arial, sans-serif;
    position: relative;
  }
  .card {
    position: absolute;
    left: 285px;
    width: 630px;
    height: 360px;
    border-radius: 22px;
    overflow: hidden;
    box-shadow: 0 10px 28px rgba(0,0,0,.45);
  }
  .card--services { top: 53px; background: var(--brand-blue); color: var(--ink-light); }
  .card--contact  { top: 467px; background: var(--paper); }

  .brand {
    position: absolute;
    display: flex;
    align-items: center;
    gap: 14px;
    font-weight: 700;
    font-size: 30px;
    letter-spacing: .5px;
    white-space: nowrap;
  }
  .brand__square { width: 34px; height: 34px; flex: none; }
  .card--services .brand { left: 48px; top: 48px; color: var(--ink-light); }
  .card--services .brand__square { background: var(--ink-light); }
  .card--contact .brand { left: 32px; top: 164px; color: var(--brand-blue); font-size: 22px; gap: 12px; letter-spacing: .2px; }
  .card--contact .brand__square { background: var(--brand-blue); width: 26px; height: 26px; }

  .services {
    position: absolute;
    left: 58px;
    top: 150px;
    list-style: none;
    font-size: 19px;
    line-height: 33px;
  }
  .services li { display: flex; align-items: center; gap: 14px; }
  .services li::before {
    content: "";
    width: 10px; height: 10px;
    border-radius: 50%;
    background: var(--ink-light);
    flex: none;
  }

  .contact-shape { position: absolute; inset: 0; width: 630px; height: 360px; }
  .contact {
    position: absolute;
    left: 362px;
    top: 42px;
    width: 250px;
    color: var(--ink-light);
    font-size: 13px;
    line-height: 18px;
    white-space: nowrap;
  }
  .contact__name { font-size: 20px; font-weight: 700; line-height: 24px; }
  .contact__role { font-size: 14px; margin-bottom: 24px; }
  .contact__address { margin-bottom: 10px; }
  .contact__label { font-weight: 700; }
  .contact__web { margin-top: 18px; font-weight: 700; font-size: 14px; }
</style>
</head>
<body>

  <section class="card card--services" aria-label="Business card, services side">
    <div class="brand"><span class="brand__square"></span>BuildMark Solutions</div>
    <ul class="services">
      <li>New Software Implementations</li>
      <li>Software Re-Implementations</li>
      <li>Redesigning Software Usage at the User Level</li>
      <li>Project Coordination &amp; Management</li>
      <li>Continued Software Support</li>
    </ul>
  </section>

  <section class="card card--contact" aria-label="Business card, contact side">
    <svg class="contact-shape" viewBox="0 0 630 360" aria-hidden="true">
      <path d="M248 0 Q366 170 286 360" fill="none" stroke="var(--arc-grey)" stroke-width="10"/>
      <path d="M260 0 Q380 170 300 360 L630 360 L630 0 Z" fill="var(--brand-blue)"/>
    </svg>
    <div class="brand"><span class="brand__square"></span>BuildMark Solutions</div>
    <div class="contact">
      <p class="contact__name">Dana R. Whitfield</p>
      <p class="contact__role">Owner</p>
      <p class="contact__address">14B Harbor Lane<br>Suite 210<br>Millbrook NY 10000</p>
      <p><span class="contact__label">O:</span> 800-555-0142 ext.100</p>
      <p><span class="contact__label">C:</span> 555-555-0178</p>
      <p><span class="contact__label">E:</span> dana@buildmark-solutions.example</p>
      <p class="contact__web">www.buildmark-solutions.example</p>
    </div>
  </section>

</body>
</html>
```